Professional & attention grabbing.

A business card design, front and back. I already have a logo I will attach, but I am open to something new as well.
Things to include:
Name:
Title:
Phone:
Email:
Wanting something that is professional but attention grabbing.
Also we do a lot of work using drones on natural gas pipelines (leading the future)if you want to include any of that. I'm open to ideas.
Target Market(s)
Natural gas transmission industry / greenhouse gas mitigation industry
Industry/Entity Type
Business
Colors
Designer to choose colors to be used in the design.
Look and feel
Each slider illustrates characteristics of the customer's brand and the style your logo design should communicate.

```html
<!DOCTYPE html>
<html lang="en">
<head>
<meta charset="utf-8">
<title>Quellmarsh Inspections – Business Card</title>
<link rel="stylesheet" href="https://fonts.googleapis.com/css2?family=Source+Sans+3:ital,wght@0,400;0,600;0,700;1,400&display=swap">
<style>
  :root {
    --backdrop: #5b4a3b;
    --card-white: #ffffff;
    --brand-red: #c42026;
    --charcoal: #38383b;
    --ink: #333336;
    --paper-text: #ffffff;
    --shadow: rgba(0, 0, 0, 0.35);
  }
  * { margin: 0; padding: 0; box-sizing: border-box; }
  html, body {
    width: 1200px;
    height: 987px;
    overflow: hidden;
    background: var(--backdrop);
    font-family: "Source Sans 3", "Helvetica Neue", Arial, sans-serif;
  }
  .canvas { position: relative; width: 1200px; height: 987px; }

  .card {
    position: absolute;
    left: 293px;
    width: 615px;
    height: 352px;
    box-shadow: 0 2px 4px var(--shadow);
  }
  .card--front { top: 130px; background: var(--card-white); }
  .card--back { top: 506px; background: var(--charcoal); }

  .front-brand {
    position: absolute;
    left: 0; top: 0;
    width: 318px; height: 100%;
    display: flex; align-items: center; justify-content: center;
  }
  .front-divider {
    position: absolute;
    left: 317px; top: 0;
    width: 2px; height: 100%;
    background: var(--ink);
  }
  .front-details {
    position: absolute;
    left: 321px; top: 0;
    right: 0; height: 100%;
    background: var(--brand-red);
    color: var(--paper-text);
  }

  .brand-lockup { display: flex; align-items: center; gap: 12px; }
  .brand-mark { width: 30px; height: 30px; background: var(--brand-red); flex: none; }
  .brand-name {
    font-weight: 700;
    font-size: 27px;
    line-height: 0.98;
    letter-spacing: 0.4px;
    text-transform: uppercase;
    color: var(--ink);
  }
  .card--back .brand-name { color: var(--paper-text); font-size: 38px; }
  .card--back .brand-mark { width: 42px; height: 42px; }

  .person-name {
    position: absolute;
    left: 40px; top: 100px;
    font-size: 22px; font-weight: 600;
    line-height: 28px;
    letter-spacing: 0.3px;
    text-transform: uppercase;
  }
  .person-title {
    position: absolute;
    left: 40px; top: 127px;
    font-size: 17px; font-weight: 400;
    line-height: 22px;
  }
  .contact-list {
    position: absolute;
    left: 40px; top: 176px;
    list-style: none;
    font-size: 16px;
    line-height: 24px;
  }
  .contact-list li { display: flex; align-items: center; gap: 8px; }
  .contact-list svg { width: 14px; height: 14px; flex: none; fill: var(--paper-text); }

  .back-brand {
    position: absolute;
    left: 0; right: 0; top: 136px;
    display: flex; justify-content: center;
  }
  .back-web {
    position: absolute;
    left: 0; right: 0; top: 292px;
    text-align: center;
    color: var(--paper-text);
    font-style: italic;
    font-size: 16px;
    letter-spacing: 4.5px;
  }
</style>
</head>
<body>
<main class="canvas">
  <section class="card card--front">
    <div class="front-brand">
      <div class="brand-lockup">
        <span class="brand-mark"></span>
        <span class="brand-name">Quellmarsh<br>Inspections</span>
      </div>
    </div>
    <div class="front-divider"></div>
    <div class="front-details">
      <p class="person-name">Dana Whitfield</p>
      <p class="person-title">CEO/Founder</p>
      <ul class="contact-list">
        <li>
          <svg viewBox="0 0 16 16" aria-hidden="true"><path d="M3.6 1l2.6 2.6-1.5 2.1c.9 1.9 2.6 3.6 4.6 4.6l2.1-1.5L14 11.4 12.4 15C6.3 14.6 1.4 9.7 1 3.6z"/></svg>
          555 014 2290
        </li>
        <li>
          <svg viewBox="0 0 16 16" aria-hidden="true"><path d="M1 3h14v10H1z M1 3l7 6 7-6" fill="none" stroke="#fff" stroke-width="1.6"/><path d="M1 3h14L8 8.5z"/></svg>
          dana@quellmarsh-insp.com
        </li>
        <li>
          <svg viewBox="0 0 16 16" aria-hidden="true"><circle cx="8" cy="8" r="7"/><path d="M4 5c1.5 0 2 1 3 1s.5 2-.5 2.5S5 11 6 12.5M10 3.5c-.5 1 .5 2 1.5 2s1.5 1.5.5 2.5-1 2 0 3" fill="none" stroke="#c42026" stroke-width="1.3"/></svg>
          www.quellmarsh-insp.com
        </li>
      </ul>
    </div>
  </section>

  <section class="card card--back">
    <div class="back-brand">
      <div class="brand-lockup">
        <span class="brand-mark"></span>
        <span class="brand-name">Quellmarsh<br>Inspections</span>
      </div>
    </div>
    <p class="back-web">www.quellmarsh-insp.com</p>
  </section>
</main>
</body>
</html>
```